Lifestyle Coaching comp needs wordpress design. We focus on strong mindsets, fitness and nutrition

BrenVigor Lifestyle Coaching needs a wordpress site. Our tagline for now (may change) is Mindset Mastery.Fitness Badassery. Sustainable Nutrition
Our logo is below. Would like to see some complimentary colors to liven it up. Clients need to come to site and get immediate professional, but fun feel. They need to have the impression that we are the last destination in their journey to wellness. Blogging, workout videos, pictures

Target Market(s)

Mostly women ages 20+

Industry/Entity Type

Nutrition

Colors
33a6d7
86cae7
ceeaf6
cfdeed
5c5c5c
cbcbcb
474747

Requirements
Must have
• A strong, badass feel :) While not being intimidating
Nice to have
• Fun fonts. Love the font in my logo
Should not have
• Pics, logos of flowers, heads, fruit.

```html
<!DOCTYPE html>
<html lang="en">
<head>
<meta charset="utf-8">
<title>BrenVigor Lifestyle Coaching</title>
<link href="https://fonts.googleapis.com/css2?family=Lato:wght@300;400;700;900&family=Open+Sans:wght@400;600;700&display=swap" rel="stylesheet">
<style>
:root{
  --blue:#33a6d7;
  --blue-light:#86cae7;
  --blue-pale:#ceeaf6;
  --blue-grey:#cfdeed;
  --text:#5c5c5c;
  --rule:#cbcbcb;
  --dark:#474747;
  --navy:#22344f;
  --white:#ffffff;
  --panel:#f2f2f2;
}
*{box-sizing:border-box;margin:0;padding:0}
html,body{width:1200px;height:2816px;overflow:hidden}
body{font-family:"Lato",sans-serif;color:var(--text);background:var(--white);position:relative}
.page{position:relative;width:1200px;height:2816px}

/* header */
.site-header{height:148px;position:relative;border-bottom:1px solid #e6e6e6}
.brand{position:absolute;left:58px;top:22px;display:flex;align-items:center;gap:14px}
.brand-mark{width:34px;height:34px;background:var(--blue)}
.brand-name{font-family:"Lato",sans-serif;font-weight:900;font-size:44px;color:var(--blue);letter-spacing:2px;line-height:1}
.brand-sub{position:absolute;left:106px;top:74px;font-size:14px;letter-spacing:5px;text-transform:uppercase;color:var(--blue);font-weight:700}
.search{position:absolute;left:728px;top:36px;width:272px;height:32px;border:1px solid var(--rule);font-size:14px;color:#999;padding:7px 10px}
.btn-login{position:absolute;left:1016px;top:36px;width:124px;height:32px;background:var(--blue);color:var(--white);font-size:14px;text-align:center;line-height:32px}
.main-nav{position:absolute;right:52px;top:96px;display:flex;gap:8px}
.main-nav a{font-size:15px;color:var(--text);text-decoration:none;padding:6px 18px;border:1px solid transparent}
.main-nav a.current{border-color:var(--blue);color:var(--blue)}

/* hero */
.hero{position:relative;height:572px;overflow:hidden;background:linear-gradient(180deg,#9bb5c2 0%,#c8d3d6 45%,#e2dccd 72%,#cfc0a4 100%)}
.hero-photo{position:absolute;inset:0}
.hero-tagline{position:absolute;left:60px;top:210px;display:flex;flex-direction:column;gap:6px}
.hero-tagline span{display:inline-block;align-self:flex-start;background:rgba(40,40,40,.82);color:var(--white);font-family:"Open Sans",sans-serif;font-weight:700;font-size:44px;line-height:56px;padding:0 16px;letter-spacing:1px}
.hero-arrow{position:absolute;top:268px}
.hero-arrow.prev{left:18px}
.hero-arrow.next{right:18px}

/* section heads */
.section-title{display:flex;align-items:center;justify-content:center;gap:28px;font-size:34px;font-weight:700;color:var(--dark)}
.section-title::before,.section-title::after{content:"";width:88px;height:2px;background:var(--dark)}
.lead{font-size:15px;line-height:24px;text-align:center;color:var(--text)}

.about{position:absolute;top:748px;left:0;width:1200px}
.about .lead{width:880px;margin:26px auto 0}

.features{position:absolute;top:940px;left:60px;width:1080px;display:flex;justify-content:space-between}
.feature{width:320px}
.feature h3{font-size:19px;font-weight:700;color:var(--dark);margin-bottom:18px}
.feature-body{display:flex;gap:14px}
.feature-body svg{flex:0 0 58px}
.feature p{font-size:14px;line-height:20px}

.videos{position:absolute;top:1128px;left:60px;width:1080px;display:flex;gap:22px}
.videos-intro{width:230px}
.videos-intro h2{font-size:30px;font-weight:700;color:var(--dark);margin-bottom:14px}
.videos-intro p{font-size:13px;line-height:19px}
.video-card{width:258px}
.video-thumb{height:172px;position:relative}
.video-card p{font-size:13px;margin-top:8px;color:var(--dark)}

.newsletter{position:absolute;top:1420px;left:60px;width:1080px;height:62px;background:var(--blue);display:flex;align-items:center}
.newsletter-label{color:var(--white);font-size:22px;padding-left:56px;width:390px}
.newsletter input{height:30px;border:none;padding:0 10px;font-family:"Lato",sans-serif;font-size:13px;margin-right:18px}
.newsletter .f-name{width:210px}
.newsletter .f-email{width:210px}
.btn-subscribe{margin-left:auto;height:62px;width:186px;background:var(--dark);color:var(--white);font-size:20px;text-align:center;line-height:62px}

.block-head{display:flex;align-items:center;gap:16px}
.block-head h2{font-size:40px;font-weight:400;color:var(--dark)}
.block-head .rule{flex:1;height:1px;background:var(--rule)}
.pager{display:flex;gap:8px}

.blog{position:absolute;top:1520px;left:60px;width:1080px}
.blog-grid{display:flex;justify-content:space-between;margin-top:34px}
.post{width:344px}
.post-thumb{height:208px}
.post h3{font-size:15px;font-weight:700;color:var(--dark);margin-top:14px}
.post .meta{font-size:12px;color:#999;margin-top:6px}

.gallery{position:absolute;top:1890px;left:60px;width:1080px}
.filters{display:flex;gap:30px;margin-top:24px;font-size:14px}
.filters span:first-child{color:var(--dark);font-weight:700}
.gallery-grid{display:flex;justify-content:space-between;margin-top:22px}
.gallery-grid div{width:258px;height:178px}

.contact{position:absolute;top:2248px;left:0;width:1200px;height:474px;background:var(--panel)}
.contact .section-title{margin-top:36px}
.contact .lead{width:780px;margin:30px auto 0;color:var(--dark)}
.contact-info{position:absolute;left:140px;top:190px}
.contact-info dt{font-size:14px;letter-spacing:4px;color:#888;text-transform:uppercase;margin-top:26px}
.contact-info dt:first-child{margin-top:0}
.contact-info dd{font-size:14px;color:var(--dark);margin-top:4px;line-height:19px}
.contact-form{position:absolute;left:456px;top:170px;width:616px;height:230px;background:var(--white);border:1px solid #e2e2e2;padding:30px}
.field{position:absolute;border:1px solid var(--rule);font-size:11px;color:#888;padding:9px;height:32px;width:242px}
.field.name{left:30px;top:30px}
.field.email{left:30px;top:82px}
.field.subject{left:30px;top:134px}
.field.message{left:300px;top:30px;width:286px;height:104px}
.btn-send{position:absolute;left:300px;top:148px;width:286px;height:32px;background:var(--blue);color:var(--white);font-size:12px;font-weight:700;text-align:center;line-height:32px;letter-spacing:1px}
.contact-note{position:absolute;top:420px;width:1200px;text-align:center;font-size:11px;letter-spacing:1px;color:#888}

.site-footer{position:absolute;top:2722px;left:0;width:1200px;height:94px;background:var(--navy);display:flex;align-items:center;padding:0 52px;color:var(--white);font-size:14px}
.social{margin-left:auto;display:flex;gap:10px}
.social span{width:26px;height:26px;border-radius:50%;background:var(--blue)}
.social span:first-child{background:#d24a3c}
</style>
</head>
<body>
<div class="page">

<header class="site-header">
  <div class="brand"><span class="brand-mark"></span><span class="brand-name">BRENVIGOR</span></div>
  <div class="brand-sub">Lifestyle Coaching</div>
  <div class="search">Search for</div>
  <div class="btn-login">Login / Register</div>
  <nav class="main-nav">
    <a class="current" href="#">Home</a><a href="#">About Us</a><a href="#">Services</a><a href="#">Blog</a><a href="#">Gallery</a><a href="#">Contact Us</a>
  </nav>
</header>

<section class="hero">
  <div class="hero-photo" role="img" aria-label="Photo of a man swinging a child on a beach"></div>
  <div class="hero-tagline"><span>Mindset Mastery.</span><span>Fitness Badassery.</span><span>Sustainable Nutrition</span></div>
  <svg class="hero-arrow prev" width="20" height="36" viewBox="0 0 20 36"><path d="M16 4 4 18l12 14" fill="none" stroke="#fff" stroke-width="4"/></svg>
  <svg class="hero-arrow next" width="20" height="36" viewBox="0 0 20 36"><path d="M4 4l12 14L4 32" fill="none" stroke="#fff" stroke-width="4"/></svg>
</section>

<section class="about">
  <h2 class="section-title">About Us</h2>
  <p class="lead">Harbor Lane Wellness Group is a coaching company that is fully insured and bonded. Our highly trained coaches work with every client to build lasting habits, stronger minds and healthier bodies. We provide guidance as required by our customers, with programs that fit real lives, busy schedules and every level of fitness. Each plan is built around you, and our team stays with you from the first session to the final goal.</p>
</section>

<section class="features">
  <div class="feature">
    <h3>Strong Mindsets</h3>
    <div class="feature-body">
      <svg width="58" height="44" viewBox="0 0 58 44"><circle cx="29" cy="22" r="18" fill="none" stroke="#5c5c5c" stroke-width="3"/><circle cx="29" cy="22" r="6" fill="#5c5c5c"/></svg>
      <p>Build focus and confidence with daily practice, clear goals and a coach who keeps you moving forward.</p>
    </div>
  </div>
  <div class="feature">
    <h3>Fitness</h3>
    <div class="feature-body">
      <svg width="58" height="44" viewBox="0 0 58 44"><rect x="4" y="12" width="8" height="20" fill="#5c5c5c"/><rect x="46" y="12" width="8" height="20" fill="#5c5c5c"/><rect x="12" y="19" width="34" height="6" fill="#5c5c5c"/></svg>
      <p>Training plans made for your body, with strength, cardio and mobility work that grows with you.</p>
    </div>
  </div>
  <div class="feature">
    <h3>Nutrition</h3>
    <div class="feature-body">
      <svg width="58" height="44" viewBox="0 0 58 44"><path d="M18 4v36M12 4v12q6 6 12 0V4M40 4v36M40 4q8 8 0 18" fill="none" stroke="#5c5c5c" stroke-width="3"/></svg>
      <p>Simple, lasting eating habits that fuel your days without strict rules or endless counting.</p>
    </div>
  </div>
</section>

<section class="videos">
  <div class="videos-intro">
    <h2>workout videos</h2>
    <p>Short guided sessions you can follow at home or in the gym. New routines every week, from quick warm ups to full strength circuits, made for every level and schedule.</p>
  </div>
  <div class="video-card">
    <div class="video-thumb" role="img" aria-label="Video still of a woman doing a kettlebell workout" style="background:linear-gradient(135deg,#6d6f73,#2e2f33)"></div>
    <p>Lorem ipsum dolor sit</p>
  </div>
  <div class="video-card">
    <div class="video-thumb" role="img" aria-label="Video still of a woman stretching outdoors" style="background:linear-gradient(135deg,#8fa4ad,#3f4b52)"></div>
    <p>Core routine for beginners</p>
  </div>
  <div class="video-card">
    <div class="video-thumb" role="img" aria-label="Video still of a dumbbell training session" style="background:linear-gradient(135deg,#9a8f86,#3a3634)"></div>
    <p>Lorem ipsum dolor sit</p>
  </div>
</section>

<section class="newsletter">
  <div class="newsletter-label">Signup for our free newsletter</div>
  <input class="f-name" type="text" placeholder="Name">
  <input class="f-email" type="text" placeholder="Email">
  <div class="btn-subscribe">Subscribe Now</div>
</section>

<section class="blog">
  <div class="block-head">
    <svg width="24" height="24" viewBox="0 0 24 24"><rect x="2" y="2" width="20" height="20" fill="none" stroke="#5c5c5c" stroke-width="2"/><path d="M6 8h12M6 12h12M6 16h8" stroke="#5c5c5c" stroke-width="2"/></svg>
    <h2>Latest Blog</h2><span class="rule"></span>
    <div class="pager"><svg width="22" height="22" viewBox="0 0 22 22"><circle cx="11" cy="11" r="10" fill="none" stroke="#cbcbcb"/><path d="M13 6 8 11l5 5" fill="none" stroke="#999" stroke-width="2"/></svg><svg width="22" height="22" viewBox="0 0 22 22"><circle cx="11" cy="11" r="10" fill="none" stroke="#cbcbcb"/><path d="M9 6l5 5-5 5" fill="none" stroke="#999" stroke-width="2"/></svg></div>
  </div>
  <div class="blog-grid">
    <article class="post"><div class="post-thumb" role="img" aria-label="Photo of a dumbbell rack in a gym" style="background:linear-gradient(135deg,#bfbfbf,#4a4a4a)"></div><h3>Post great and long name</h3><p class="meta">Posted by coach · 12 comments</p></article>
    <article class="post"><div class="post-thumb" role="img" aria-label="Photo of a runner on a stormy road" style="background:linear-gradient(180deg,#7c8791,#3b3e42)"></div><h3>Post great and long name</h3><p class="meta">Posted by coach · 8 comments</p></article>
    <article class="post"><div class="post-thumb" role="img" aria-label="Black and white photo of a fitness pair" style="background:linear-gradient(135deg,#9a9a9a,#1e1e1e)"></div><h3>Post great and long name</h3><p class="meta">Posted by coach · 5 comments</p></article>
  </div>
</section>

<section class="gallery">
  <div class="block-head">
    <svg width="24" height="24" viewBox="0 0 24 24"><rect x="2" y="4" width="20" height="16" fill="none" stroke="#5c5c5c" stroke-width="2"/><path d="M4 18l6-7 4 4 3-3 5 6" fill="none" stroke="#5c5c5c" stroke-width="2"/></svg>
    <h2>Photo Gallery</h2><span class="rule"></span>
    <div class="pager"><svg width="22" height="22" viewBox="0 0 22 22"><circle cx="11" cy="11" r="10" fill="none" stroke="#cbcbcb"/><path d="M13 6 8 11l5 5" fill="none" stroke="#999" stroke-width="2"/></svg><svg width="22" height="22" viewBox="0 0 22 22"><circle cx="11" cy="11" r="10" fill="none" stroke="#cbcbcb"/><path d="M9 6l5 5-5 5" fill="none" stroke="#999" stroke-width="2"/></svg></div>
  </div>
  <div class="filters"><span>All</span><span>Fitness</span><span>Nutrition</span><span>Lifestyle</span></div>
  <div class="gallery-grid">
    <div role="img" aria-label="Photo of a woman lifting a barbell" style="background:linear-gradient(135deg,#c9b9a5,#4d6a80)"></div>
    <div role="img" aria-label="Photo of a group exercise class" style="background:linear-gradient(135deg,#e3c9b8,#8a6e60)"></div>
    <div role="img" aria-label="Photo of a woman training with weights" style="background:linear-gradient(135deg,#d8b59a,#7d5440)"></div>
    <div role="img" aria-label="Photo of a runner on a sunny country path" style="background:linear-gradient(135deg,#e9d7a8,#6b8a4e)"></div>
  </div>
</section>

<section class="contact">
  <h2 class="section-title">Get In Touch</h2>
  <p class="lead">Lorem ipsum dolor sit amet, consectetur adipiscing elit, sed do eiusmod tempor incididunt ut labore et dolore magna aliqua. Ut enim ad minim veniam, quis nostrud exercitation ullamco laboris nisi ut aliquip ex.</p>
  <dl class="contact-info">
    <dt>Call Me</dt><dd>(555) 014-2380</dd>
    <dt>Email Me</dt><dd>hello@brenvigor-coaching.com</dd>
    <dt>Address</dt><dd>72 Larkfield Ridge Road<br>Westbrook, CA 90000</dd>
  </dl>
  <div class="contact-form">
    <div class="field name">NAME</div>
    <div class="field email">EMAIL</div>
    <div class="field subject">SUBJECT</div>
    <div class="field message">TEXT</div>
    <div class="btn-send">SEND NOW</div>
  </div>
  <p class="contact-note">LOOKING FORWARD TO HEARING FROM YOU</p>
</section>

<footer class="site-footer">
  <span>Copyright © 2015 BrenVigor All rights reserved</span>
  <div class="social"><span></span><span></span><span></span><span></span></div>
</footer>

</div>
</body>
</html>
```